Flat Belly Design Graphics for Social

I want to create 9 social media graphics (new Instagram size 4:5 (1080 x 1350 pixels) focusing on our Flat Belly Graphics, using the pics attached. Use the attached pics, NO RANDOM STOCK PHOTOGRAPHY. For the color scheme of the graphics, the color palette is attached. YOU MUST POST ALL 9 GRAPHICS IN ONE ENTRY.
Using the 3 titles below, create one set of graphics. 1) with all text, then for the others, use the pictures as detailed below in IMPORTANT:
1. Ten-Week Bright Morning Reboot
2. The Quick Garden Kitchen Menu Guide
3. Studio Habits for Lasting Energy Past Midlife - Zero Gym Needed
IMPORTANT:
Only use RK Pic 1 and RK Pic 2 with the title, Ten-Week Bright Morning Reboot
Only use meal plan1 and meal plan2 pics with the title, Quick Garden Kitchen Menu Guide
Only use studio habits 1 and studio habits 2 pics with the title, Studio Habits for Lasting Energy Past Midlife - Zero Gym Needed
women over 40

```html
<!DOCTYPE html>
<html lang="en">
<head>
<meta charset="utf-8">
<title>Social Graphics Set</title>
<link rel="stylesheet" href="https://fonts.googleapis.com/css2?family=Archivo+Black&family=Montserrat:wght@600;700;800&family=Oswald:wght@600;700&family=Roboto+Condensed:wght@500;700&display=swap">
<style>
:root{
  --stage:#262626;
  --green:#1b5d53;
  --green-dark:#1e3a35;
  --pink:#d2558f;
  --pink-deep:#c94e88;
  --pink-mid:#e7a1bf;
  --pink-soft:#f3c9da;
  --blush:#faeaee;
  --white:#ffffff;
}
*{margin:0;padding:0;box-sizing:border-box}
html,body{width:960px;height:1200px;overflow:hidden;background:var(--stage)}
.canvas{position:relative;width:960px;height:1200px}
.post{position:absolute;width:231px;height:289px;overflow:hidden;background:var(--blush)}
.post .bg{position:absolute;inset:0;width:100%;height:100%}
.photo{position:absolute}
.t{position:absolute;line-height:1;white-space:nowrap}
.cond{font-family:'Oswald',sans-serif;font-weight:700;letter-spacing:-.5px}
.wide{font-family:'Archivo Black',sans-serif}
.mont{font-family:'Montserrat',sans-serif;font-weight:700}
.robo{font-family:'Roboto Condensed',sans-serif;font-weight:700}
.green{color:var(--green)}
.pink{color:var(--pink)}
.white{color:var(--white)}
.right{text-align:right}
.center{left:0;right:0;text-align:center}

.c1{left:110px;top:132px}
.c2{left:363px;top:132px}
.c3{left:616px;top:132px}
.r2{top:452px}
.r3{top:772px}
.k1{left:110px}.k2{left:363px}.k3{left:616px}

.reboot-bar{position:absolute;left:13px;top:204px;width:206px;height:72px;background:linear-gradient(90deg,#d77aa6,#df8fb4)}
.reboot-bar::after{content:"";position:absolute;right:-12px;top:0;width:12px;height:84px;background:var(--pink-deep);clip-path:polygon(0 0,100% 20%,100% 100%,0 86%)}
.badge{position:absolute;left:156px;top:211px;width:82px;height:82px;border-radius:50%;background:var(--pink-soft)}
.rule{position:absolute;height:1.5px;background:var(--blush)}
</style>
</head>
<body>
<main class="canvas">

  <!-- Text only: reboot -->
  <section class="post c1">
    <svg class="bg" viewBox="0 0 231 289" preserveAspectRatio="none">
      <defs><linearGradient id="g1" x1="0" y1="0" x2="1" y2="1"><stop offset="0" stop-color="#ebacc6"/><stop offset="1" stop-color="#f6dbe5"/></linearGradient></defs>
      <rect width="231" height="289" fill="url(#g1)"/>
      <polygon points="0,0 231,0 231,46 175,97 0,24" fill="#faeaee"/>
    </svg>
    <div class="t wide green" style="right:16px;top:15px;font-size:22px;font-style:italic;transform:skewX(-8deg)">TEN-WEEK</div>
    <div class="t cond pink center" style="top:100px;font-size:40px">BRIGHT</div>
    <div class="t cond green center" style="top:146px;font-size:48px">MORNING</div>
    <div class="reboot-bar"></div>
    <div class="t wide white" style="left:13px;width:206px;top:222px;text-align:center;font-size:34px">REBOOT</div>
  </section>

  <!-- Text only: kitchen -->
  <section class="post c2">
    <svg class="bg" viewBox="0 0 231 289" preserveAspectRatio="none">
      <defs><linearGradient id="g2" x1="0" y1="0" x2="1" y2="1"><stop offset="0" stop-color="#e9a4c1"/><stop offset="1" stop-color="#f7dde7"/></linearGradient></defs>
      <rect width="231" height="289" fill="url(#g2)"/>
      <polygon points="0,199 79,124 231,211 231,289 0,289" fill="#faeaee"/>
    </svg>
    <div class="t cond green center" style="top:16px;font-size:42px">THE QUICK</div>
    <div class="t cond green center" style="top:66px;font-size:46px">GARDEN</div>
    <div class="t wide pink center" style="top:186px;font-size:30px">KITCHEN</div>
    <div class="t wide green center" style="top:228px;font-size:26px">MENU GUIDE</div>
  </section>

  <!-- Text only: studio habits -->
  <section class="post c3">
    <svg class="bg" viewBox="0 0 231 289" preserveAspectRatio="none">
      <defs><linearGradient id="g3" x1="0" y1="0" x2="1" y2="1"><stop offset="0" stop-color="#ebaac5"/><stop offset="1" stop-color="#e59abb"/></linearGradient></defs>
      <rect width="231" height="289" fill="url(#g3)"/>
      <polygon points="0,0 46,0 135,77 26,289 0,289" fill="#faeaee"/>
    </svg>
    <div class="t cond green" style="left:13px;top:62px;font-size:24px">STUDIO</div>
    <div class="t cond pink" style="left:13px;top:98px;font-size:24px">HABITS</div>
    <div class="t cond green" style="left:13px;top:134px;font-size:24px">FOR</div>
    <div class="t cond green right" style="right:14px;top:60px;font-size:28px">LASTING</div>
    <div class="t cond green right" style="right:14px;top:97px;font-size:28px">ENERGY</div>
    <div class="rule" style="left:150px;width:67px;top:141px"></div>
    <div class="t cond green right" style="right:14px;top:148px;font-size:28px">PAST</div>
    <div class="t cond green right" style="right:14px;top:185px;font-size:28px">MIDLIFE</div>
    <div class="t mont pink right" style="right:14px;top:234px;font-size:15px;font-weight:800;font-style:italic">ZERO GYM</div>
    <div class="t mont pink right" style="right:14px;top:258px;font-size:15px;font-weight:800;font-style:italic">NEEDED</div>
  </section>

  <!-- Photo: reboot 1 -->
  <section class="post k1 r2">
    <svg class="bg" viewBox="0 0 231 289" preserveAspectRatio="none">
      <defs><linearGradient id="g4" x1="0" y1="0" x2="1" y2="1"><stop offset="0" stop-color="#faeaee"/><stop offset=".55" stop-color="#f3cadb"/><stop offset="1" stop-color="#e7a1bf"/></linearGradient></defs>
      <rect width="231" height="289" fill="url(#g4)"/>
      <polygon points="0,0 70,0 100,40 0,260" fill="#faeaee"/>
    </svg>
    <div class="photo" role="img" aria-label="Smiling woman in a white cropped sweater pointing to her waist" style="left:70px;top:0;width:161px;height:222px;background:linear-gradient(180deg,#3a2a26 0%,#c79a84 30%,#f3f0ee 55%,#e3c5c9 100%);clip-path:polygon(20% 0,80% 0,95% 60%,100% 80%,85% 100%,10% 100%,0 75%,10% 55%)"></div>
    <div class="t mont pink" style="left:14px;top:26px;font-size:22px;font-weight:800">TEN</div>
    <div class="t mont green" style="left:18px;top:56px;font-size:30px;line-height:34px;white-space:normal;width:30px;text-align:center">W E E K</div>
    <div class="t wide pink center" style="top:222px;font-size:18px">BRIGHT MORNING</div>
    <div class="t wide green center" style="top:252px;font-size:22px">REBOOT</div>
  </section>

  <!-- Photo: kitchen 1 -->
  <section class="post k2 r2">
    <svg class="bg" viewBox="0 0 231 289" preserveAspectRatio="none">
      <rect width="231" height="289" fill="#f7dce6"/>
      <polygon points="0,112 82,168 231,90 231,150 82,190 0,150" fill="#e8a3c0"/>
    </svg>
    <div class="photo" role="img" aria-label="Overhead table of chicken, berries, asparagus and a printed meal plan sheet" style="inset:0;background:linear-gradient(135deg,#f1b9a6 0%,#5a3a2a 45%,#c9443f 70%,#3b2a20 100%);clip-path:polygon(0 0,100% 0,100% 31%,35% 58%,0 39%)"></div>
    <div class="t wide green center" style="top:176px;font-size:17px">THE QUICK GARDEN</div>
    <div class="t wide pink center" style="top:198px;font-size:26px">KITCHEN</div>
    <div class="t wide green center" style="top:234px;font-size:26px">MENU GUIDE</div>
  </section>

  <!-- Photo: studio habits 1 -->
  <section class="post k3 r2">
    <svg class="bg" viewBox="0 0 231 289" preserveAspectRatio="none">
      <rect width="231" height="289" fill="#faeaee"/>
    </svg>
    <div class="photo" role="img" aria-label="Two women sharing a whispered secret, one looking surprised" style="inset:0;background:linear-gradient(120deg,#3a2620 0%,#b07a5c 40%,#f2e9e6 75%,#d7a98e 100%);clip-path:polygon(0 0,100% 0,100% 70%,41% 37%,0 60%)"></div>
    <div class="t mont green" style="left:30px;top:162px;font-size:15px;font-weight:600">STUDIO HABITS</div>
    <div class="t mont green" style="left:30px;top:182px;font-size:15px;font-weight:600">FOR LASTING</div>
    <div class="t mont pink" style="left:30px;top:201px;font-size:24px;font-weight:800">Energy Past</div>
    <div class="t mont green" style="left:30px;top:229px;font-size:27px;font-weight:600">MIDLIFE</div>
    <div class="t mont green" style="left:30px;top:264px;font-size:14px;font-weight:600">ZERO GYM NEEDED</div>
  </section>

  <!-- Photo: reboot 2 -->
  <section class="post k1 r3">
    <svg class="bg" viewBox="0 0 231 289" preserveAspectRatio="none">
      <defs><linearGradient id="g7" x1="0" y1="0" x2="1" y2="1"><stop offset="0" stop-color="#6a4434"/><stop offset=".6" stop-color="#b58c77"/><stop offset="1" stop-color="#4a3128"/></linearGradient></defs>
      <rect width="231" height="289" fill="url(#g7)"/>
      <polygon points="0,0 90,0 116,28 60,235 0,262" fill="#faeaee"/>
    </svg>
    <div class="photo" role="img" aria-label="Smiling woman in a white cropped sweater pointing to her waist" style="left:20px;top:36px;width:170px;height:253px;background:linear-gradient(180deg,#2e211d 0%,#c99880 28%,#f4f1ef 50%,#cfa089 72%,#1d1a1a 100%);clip-path:polygon(35% 0,65% 0,80% 45%,100% 65%,95% 100%,5% 100%,0 65%,20% 45%)"></div>
    <div class="badge"></div>
    <div class="t cond pink" style="left:9px;top:4px;font-size:40px">TEN</div>
    <div class="t cond green" style="left:9px;top:48px;font-size:42px">WEEK</div>
    <div class="t cond right" style="right:8px;top:22px;font-size:30px;color:var(--green-dark)">BRIGHT</div>
    <div class="t cond white" style="left:8px;top:232px;font-size:32px">MORNING</div>
    <div class="t cond pink" style="left:163px;top:241px;font-size:19px">REBOOT</div>
  </section>

  <!-- Photo: kitchen 2 -->
  <section class="post k2 r3">
    <svg class="bg" viewBox="0 0 231 289" preserveAspectRatio="none">
      <rect width="231" height="289" fill="#faeaee"/>
    </svg>
    <div class="photo" role="img" aria-label="Fresh vegetables, bananas, lentils and beans on a dark wooden table" style="inset:0;background:linear-gradient(160deg,#c3302a 0%,#2c3a22 25%,#e9cd4d 40%,#3a2e28 60%,#c4572f 85%,#2a211d 100%);clip-path:polygon(0 0,100% 0,100% 33%,58% 33%,45% 50%,59% 68%,43% 64%,50% 84%,72% 100%,0 100%)"></div>
    <div class="t robo green right" style="right:8px;top:66px;font-size:30px">The</div>
    <div class="t robo green right" style="right:8px;top:98px;font-size:24px;font-weight:500">Quick Garden</div>
    <div class="t robo pink right" style="right:8px;top:124px;font-size:36px">KITCHEN</div>
    <div class="t robo pink right" style="right:8px;top:166px;font-size:38px">MENU</div>
    <div class="t robo green right" style="right:8px;top:212px;font-size:30px">Guide</div>
  </section>

  <!-- Photo: studio habits 2 -->
  <section class="post k3 r3">
    <svg class="bg" viewBox="0 0 231 289" preserveAspectRatio="none">
      <defs><linearGradient id="g9" x1="0" y1="0" x2="1" y2="1"><stop offset="0" stop-color="#f3cadb"/><stop offset="1" stop-color="#e597b8"/></linearGradient></defs>
      <rect width="231" height="289" fill="url(#g9)"/>
      <polygon points="0,0 231,0 231,26 65,112 0,57" fill="#faeaee"/>
    </svg>
    <div class="photo" role="img" aria-label="Two women whispering, one reacting with surprise" style="left:0;top:124px;width:132px;height:165px;background:linear-gradient(150deg,#3a2620 0%,#c28d72 35%,#d9b39a 60%,#8fb4cf 100%);clip-path:polygon(5% 10%,40% 0,75% 5%,100% 35%,100% 100%,0 100%)"></div>
    <div class="t mont green" style="left:22px;top:12px;font-size:23px">STUDIO HABITS</div>
    <div class="t mont green" style="left:22px;top:42px;font-size:17px;font-weight:600">FOR LASTING</div>
    <div class="t cond pink right" style="right:16px;top:88px;font-size:26px">ENERGY PAST</div>
    <div class="t mont green right" style="right:16px;top:126px;font-size:18px;font-weight:600">MIDLIFE</div>
    <div class="t wide green right" style="right:14px;top:150px;font-size:40px">ZERO</div>
    <div class="rule" style="left:138px;width:79px;top:205px;background:var(--pink-deep)"></div>
    <div class="t mont white right" style="right:16px;top:220px;font-size:12px;font-weight:600">GYM</div>
    <div class="t mont white right" style="right:16px;top:238px;font-size:12px;font-weight:600">NEEDED</div>
  </section>

</main>
</body>
</html>
```